Global Beard Oil Review Business needs a refresh

topwhiskertonic.net is a global business who's mission is to curate all available beard oils from around the world, review and grade them and present this curated collection to the user of the website.

The scope of this job includes the web site design and the design of a suitable logo to be used in the site header.

The existing site can be seen on http://topwhiskertonic.net, however this is a mock-up only the style and logo should NOT be used. This is to give you an idea of the concept of the site only.

This job is for PSD design only.

See attached design brief for detailed design requirements.
Updates

Project Deadline Extended
Reason: Extending deadline by 5 days to allow for final submissions

Target Market(s)

Men's grooming / retail

Industry/Entity Type

Retail

Number of Pages Required

2 page

Font styles to use
Sans Serif

Requirements
Must have
• 1) Comparison Table
• 2) Side Bar
• 3) Header area
• 4) Photo of Delvin Marsk (attached - can be circular or "cut-out")
• 5) Cool beard-oriented custom design background (e.g., stylistic black/brown on brown/orange beard background. I envision this beard background "drawing" rather than photo based)
• (see attached design requirements for details)
Nice to have
• Signature style writing at top with name "Delvin Marsk"
Should not have
• Do NOT use the look & feel or logo from the existing site.

```html
<!DOCTYPE html>
<html lang="en">
<head>
<meta charset="utf-8">
<title>Top Whisker Tonic</title>
<link href="https://fonts.googleapis.com/css2?family=Amatic+SC:wght@400;700&family=Raleway:wght@400;500;600;700&family=Mr+Dafoe&display=swap" rel="stylesheet">
<style>
:root{
  --orange:#f7a300;
  --maroon:#5c0808;
  --ink:#2b2b2b;
  --line:#e4e4e4;
  --paper:#ffffff;
  --pattern-light:#f4f4f4;
  --pattern-mid:#cfcfcf;
  --pattern-dark:#b4b4b4;
}
*{box-sizing:border-box;margin:0;padding:0}
html,body{width:1200px;height:2647px;overflow:hidden}
body{position:relative;font-family:'Raleway',sans-serif;color:var(--ink);background:var(--pattern-mid)}
.backdrop{position:absolute;inset:0;background:
  radial-gradient(ellipse at 15% 10%,var(--pattern-light),transparent 45%),
  radial-gradient(ellipse at 85% 35%,var(--pattern-light),transparent 45%),
  radial-gradient(ellipse at 20% 65%,var(--pattern-light),transparent 45%),
  radial-gradient(ellipse at 80% 90%,var(--pattern-light),transparent 45%),
  linear-gradient(180deg,var(--pattern-mid),var(--pattern-dark) 50%,var(--pattern-mid))}
.page{position:absolute;left:67px;top:0;width:1066px;height:2609px;background:var(--paper)}
.abs{position:absolute}

/* header */
.brand{left:79px;top:22px;display:flex;align-items:center;gap:10px}
.brand-dot{width:40px;height:40px;border-radius:50%;background:var(--orange)}
.brand-name{font-family:'Amatic SC',sans-serif;font-weight:700;font-size:44px;line-height:38px;color:var(--ink)}
.portrait{left:316px;top:0;width:160px;height:160px;border-radius:50%;border:6px solid #fff;box-shadow:0 2px 6px rgba(0,0,0,.25);background:radial-gradient(circle at 50% 40%,#8a6a58,#3d3330 75%)}
.signature{left:484px;top:28px;font-family:'Mr Dafoe',cursive;font-size:36px;color:var(--ink);transform:rotate(-4deg)}
.contact{display:flex;align-items:center;gap:12px;font-size:16px;color:var(--ink)}
.contact-icon{width:36px;height:36px;border-radius:50%;background:var(--orange);display:flex;align-items:center;justify-content:center}
.contact.mail{left:714px;top:24px}
.contact.phone{left:966px;top:24px}
.nav{left:530px;top:91px;display:flex;align-items:center;font-size:15px;font-weight:500}
.nav a{color:var(--ink);text-decoration:none;padding:4px 9px}
.nav a.current{background:var(--maroon);color:#fff;padding:4px 12px}
.nav .sep{width:4px;height:4px;border-radius:50%;background:var(--ink);margin:0 5px}
.nav a.about{margin-left:14px}

/* hero */
.hero{left:67px;top:138px;width:1066px;height:467px;background:linear-gradient(180deg,#7b6a58 0%,#5a4c40 45%,#8a3a20 70%,#3a1a12 100%)}
.hero-title{left:646px;top:226px;font-family:'Amatic SC',sans-serif;font-weight:400;font-size:64px;line-height:84px;color:#fff;letter-spacing:1px;white-space:nowrap}
.hero-btn{left:648px;top:441px;width:141px;height:53px;background:var(--orange);color:var(--ink);font-size:21px;font-weight:500;display:flex;align-items:center;justify-content:center}
.dots{left:574px;top:622px;display:flex;gap:9px;align-items:center}
.dots span{width:7px;height:7px;border-radius:50%;background:var(--ink)}
.dots span.on{width:11px;height:11px;background:#fff;border:2px solid var(--orange)}

/* welcome */
.welcome{left:67px;top:660px;width:1066px;text-align:center;font-family:'Amatic SC',sans-serif;font-weight:700;font-size:68px;color:var(--ink)}
.welcome em{font-style:normal;color:var(--maroon)}
.intro{left:158px;top:760px;width:884px;text-align:center;font-size:12.5px;line-height:21px;color:var(--ink)}

/* process */
.process{left:0;top:880px;width:1200px;height:200px}
.process svg{position:absolute;left:0;top:0}
.step{position:absolute;width:200px;text-align:center;font-family:'Amatic SC',sans-serif;font-weight:700;font-size:30px;color:var(--ink)}

/* comparison table */
.compare{left:79px;top:1101px;width:738px;border-collapse:collapse;table-layout:fixed;font-size:12.5px}
.compare th{background:var(--maroon);color:var(--orange);height:60px;font-size:13px;font-weight:700;border-right:1px solid #7c2a2a;text-align:center;line-height:16px}
.compare th:first-child{border-radius:6px 0 0 0}
.compare th:last-child{border-radius:0 6px 0 0;border-right:none}
.compare td{height:222px;border:1px solid var(--line);vertical-align:middle;padding:0 8px;color:var(--ink)}
.compare td.center{text-align:center}
.product{text-align:center}
.product-shot{width:100px;height:108px;margin:0 auto 6px}
.shot-gold{background:linear-gradient(180deg,#f4e3b4,#e3b347)}
.shot-amber{background:linear-gradient(180deg,#f5e8e0,#a5522c)}
.product-name{font-weight:700;color:var(--maroon);font-size:15px;line-height:18px}
.supplier{font-size:14px;color:var(--ink);margin-top:4px}
.scores p{line-height:29px;font-size:12.5px}
.scores b{font-weight:700}
.buy{display:inline-block;width:110px;height:40px;line-height:40px;background:var(--orange);color:#fff;font-size:15px;text-align:center}
.more{left:367px;top:2522px;width:166px;height:38px;background:#c6c6c6;color:#fff;font-size:16px;display:flex;align-items:center;justify-content:center;gap:8px}

/* sidebar */
.signup{left:854px;top:1101px;width:265px;height:341px;background:var(--orange);padding:18px 22px;text-align:center}
.signup h3{font-family:'Amatic SC',sans-serif;font-weight:700;font-size:38px;line-height:42px;color:var(--maroon)}
.signup p{font-size:13px;line-height:18px;color:var(--ink);margin-top:12px}
.signup .field{margin-top:14px;height:36px;background:#fff;font-size:11px;color:#888;display:flex;align-items:center;justify-content:center}
.signup .submit{margin-top:14px;height:36px;background:var(--maroon);color:#fff;font-size:13px;font-weight:700;display:flex;align-items:center;justify-content:center}
.signup small{display:block;margin-top:12px;font-size:10px;line-height:14px;color:#fff}
.blog-title{left:854px;top:1490px;font-family:'Amatic SC',sans-serif;font-weight:700;font-size:40px;color:var(--maroon)}
.posts{left:854px;top:1554px;width:265px;list-style:none}
.posts li{display:flex;gap:12px;height:139px;border-bottom:1px solid var(--line)}
.posts li:last-child{border-bottom:none}
.thumb{width:88px;height:88px;flex:none}
.post-title{font-weight:700;font-size:16px;line-height:24px;color:var(--orange)}
.post-date{font-size:12.5px;color:var(--ink);margin-top:6px}

/* footer */
.footer{left:58px;top:2609px;width:1084px;height:38px;background:var(--orange);display:flex;align-items:center;justify-content:space-between;padding:0 20px 0 74px;font-size:12px;color:#fff}
.social{display:flex;gap:14px}
.social span{width:14px;height:14px;border-radius:50%;background:var(--maroon)}
</style>
</head>
<body>
<div class="backdrop" role="img" aria-label="Custom background pattern of white and grey drawn bearded faces with glasses and moustaches"></div>
<div class="page"></div>

<header>
  <div class="abs brand"><span class="brand-dot"></span><span class="brand-name">Top Whisker<br>Tonic</span></div>
  <div class="abs portrait" role="img" aria-label="Circular portrait photo of Delvin Marsk"></div>
  <div class="abs signature">Delvin Marsk</div>
  <div class="abs contact mail"><span class="contact-icon"><svg width="18" height="18" viewBox="0 0 24 24"><path d="M6.6 10.8c1.4 2.8 3.8 5.1 6.6 6.6l2.2-2.2c.3-.3.7-.4 1-.2 1.1.4 2.3.6 3.6.6.6 0 1 .4 1 1V20c0 .6-.4 1-1 1C10.6 21 3 13.4 3 4c0-.6.4-1 1-1h3.5c.6 0 1 .4 1 1 0 1.3.2 2.5.6 3.6.1.3 0 .7-.2 1z" fill="#5c0808"/></svg></span>info@topwhiskertonic.net</div>
  <div class="abs contact phone"><span class="contact-icon"><svg width="18" height="14" viewBox="0 0 24 18"><rect x="1" y="1" width="22" height="16" rx="1" fill="#5c0808"/><path d="M2 2l10 8 10-8" stroke="#f7a300" stroke-width="2" fill="none"/></svg></span>123-456-7890</div>
  <nav class="abs nav">
    <a class="current" href="#">Home</a>
    <a class="about" href="#">About</a><span class="sep"></span>
    <a href="#">Our Charter</a><span class="sep"></span>
    <a href="#">Beard Oil Review Methodology</a><span class="sep"></span>
    <a href="#">Blog</a>
  </nav>
</header>

<section>
  <div class="abs hero" role="img" aria-label="Photo of a Timberline beard oil bottle resting on a plaid flannel shirt"></div>
  <h1 class="abs hero-title">Curate, Review &amp; Grade<br>Then Present</h1>
  <a class="abs hero-btn">See Table</a>
  <div class="abs dots"><span class="on"></span><span></span><span></span><span></span></div>
</section>

<section>
  <h2 class="abs welcome">Welcome To <em>Top Whisker Tonic</em></h2>
  <p class="abs intro">We are a global business with the mission is to curate all available beard oils from around the world, review &amp; grade them &amp; present this curated collection to the users of the site. Our Target Audience are all grooming men. Lorem ipsum dolor sit amet, consectetuer adipiscing elit, sed diam nonummy nibh euismod tincidunt ut laoreet dolore magna aliquam erat volutpat. Ut wisi enim ad minim veniam, quis nostrud exerci tation ullamcorper susci. Ut wisi enim ad minim veniam, quis nostrud exerci tation ullamcorper susci.</p>
  <div class="abs process">
    <svg width="1200" height="200" viewBox="0 0 1200 200">
      <defs>
        <path id="arc-one" d="M288 90 C 370 150, 460 150, 536 80"/>
        <path id="arc-two" d="M660 40 C 740 -5, 850 0, 910 60"/>
      </defs>
      <use href="#arc-one" fill="none" stroke="#2b2b2b" stroke-width="2" stroke-dasharray="2 5"/>
      <use href="#arc-two" fill="none" stroke="#2b2b2b" stroke-width="2" stroke-dasharray="2 5"/>
      <path d="M528 78 l10 0 -2 10" fill="none" stroke="#2b2b2b" stroke-width="2"/>
      <path d="M900 60 l10 2 0 -10" fill="none" stroke="#2b2b2b" stroke-width="2"/>
      <text font-family="Raleway, sans-serif" font-size="13" fill="#5c0808" dy="-8"><textPath href="#arc-one" startOffset="16%">We curate all available beard oils</textPath></text>
      <text font-family="Raleway, sans-serif" font-size="13" fill="#5c0808" dy="-8"><textPath href="#arc-two" startOffset="12%">Review &amp; Grade them &amp; Present</textPath></text>
      <circle cx="226" cy="70" r="55" fill="#f7a300"/>
      <path d="M200 72 l18 18 34 -38" fill="none" stroke="#5c0808" stroke-width="9" stroke-linecap="round" stroke-linejoin="round"/>
      <circle cx="597" cy="70" r="55" fill="#f7a300"/>
      <circle cx="597" cy="70" r="30" fill="none" stroke="#5c0808" stroke-width="4"/>
      <path d="M597 50 l6 13 14 1 -11 9 4 14 -13 -8 -13 8 4 -14 -11 -9 14 -1z" fill="#5c0808"/>
      <circle cx="971" cy="70" r="55" fill="#f7a300"/>
      <rect x="945" y="46" width="52" height="44" rx="3" fill="none" stroke="#5c0808" stroke-width="4"/>
      <line x1="945" y1="56" x2="997" y2="56" stroke="#5c0808" stroke-width="4"/>
      <path d="M971 96 v-28 m-11 11 l11 -11 11 11" fill="none" stroke="#5c0808" stroke-width="4"/>
    </svg>
    <div class="step" style="left:126px;top:134px">Curate</div>
    <div class="step" style="left:497px;top:134px">Review &amp; Grade</div>
    <div class="step" style="left:871px;top:134px">Present</div>
  </div>
</section>

<main>
  <table class="abs compare">
    <colgroup><col style="width:134px"><col style="width:72px"><col style="width:90px"><col style="width:99px"><col style="width:64px"><col style="width:152px"><col style="width:127px"></colgroup>
    <thead><tr><th>Product,<br>Supplier</th><th>Origin ▾</th><th>Base Oil ▾</th><th>Scent ▾</th><th>Aroma</th><th>Therapeutic Affect,<br>Value, Over All</th><th>Get It</th></tr></thead>
    <tbody>
      <tr><td class="product"><div class="product-shot shot-gold" role="img" aria-label="Trail-Kit beard oil bottle with cloth pouch"></div><div class="product-name">Trail-Kit</div><div class="supplier">Bristle &amp; Co.</div></td><td>USA</td><td class="center">Jojoba,<br>Hempseed</td><td>Spice Market</td><td>5</td><td class="scores"><p><b>Therapeutic Affect:</b> 6</p><p><b>Value:</b> 6</p><p><b>Over All:</b> 5</p></td><td class="center"><a class="buy">Buy Now</a></td></tr>
      <tr><td class="product"><div class="product-shot shot-amber" role="img" aria-label="Harbor Leaf Tonic amber dropper bottle"></div><div class="product-name">Harbor Leaf<br>Tonic</div><div class="supplier">Bristle &amp; Co.</div></td><td>USA</td><td class="center">Jojoba,<br>Hempseed</td><td>Spice Market</td><td>5</td><td class="scores"><p><b>Therapeutic Affect:</b> 6</p><p><b>Value:</b> 6</p><p><b>Over All:</b> 5</p></td><td class="center"><a class="buy">Buy Now</a></td></tr>
      <tr><td class="product"><div class="product-shot shot-gold" role="img" aria-label="Trail-Kit beard oil bottle with cloth pouch"></div><div class="product-name">Trail-Kit</div><div class="supplier">Bristle &amp; Co.</div></td><td>USA</td><td class="center">Jojoba,<br>Hempseed</td><td>Spice Market</td><td>5</td><td class="scores"><p><b>Therapeutic Affect:</b> 6</p><p><b>Value:</b> 6</p><p><b>Over All:</b> 5</p></td><td class="center"><a class="buy">Buy Now</a></td></tr>
      <tr><td class="product"><div class="product-shot shot-amber" role="img" aria-label="Harbor Leaf Tonic amber dropper bottle"></div><div class="product-name">Harbor Leaf<br>Tonic</div><div class="supplier">Bristle &amp; Co.</div></td><td>USA</td><td class="center">Jojoba,<br>Hempseed</td><td>Spice Market</td><td>5</td><td class="scores"><p><b>Therapeutic Affect:</b> 6</p><p><b>Value:</b> 6</p><p><b>Over All:</b> 5</p></td><td class="center"><a class="buy">Buy Now</a></td></tr>
      <tr><td class="product"><div class="product-shot shot-gold" role="img" aria-label="Trail-Kit beard oil bottle with cloth pouch"></div><div class="product-name">Trail-Kit</div><div class="supplier">Bristle &amp; Co.</div></td><td>USA</td><td class="center">Jojoba,<br>Hempseed</td><td>Spice Market</td><td>5</td><td class="scores"><p><b>Therapeutic Affect:</b> 6</p><p><b>Value:</b> 6</p><p><b>Over All:</b> 5</p></td><td class="center"><a class="buy">Buy Now</a></td></tr>
      <tr><td class="product"><div class="product-shot shot-amber" role="img" aria-label="Harbor Leaf Tonic amber dropper bottle"></div><div class="product-name">Harbor Leaf<br>Tonic</div><div class="supplier">Bristle &amp; Co.</div></td><td>USA</td><td class="center">Jojoba,<br>Hempseed</td><td>Spice Market</td><td>5</td><td class="scores"><p><b>Therapeutic Affect:</b> 6</p><p><b>Value:</b> 6</p><p><b>Over All:</b> 5</p></td><td class="center"><a class="buy">Buy Now</a></td></tr>
    </tbody>
  </table>
  <div class="abs more"><svg width="18" height="18" viewBox="0 0 24 24"><path d="M20 12a8 8 0 1 1-3-6.2" fill="none" stroke="#fff" stroke-width="3"/><path d="M18 2v5h-5" fill="none" stroke="#fff" stroke-width="3"/></svg>Loading More...</div>
</main>

<aside>
  <div class="abs signup">
    <h3>Get More Stuff Like This In Your InBox</h3>
    <p>Subscribe to our mailing list &amp; get interesting stuff &amp; updates.</p>
    <div class="field">Enter your email here</div>
    <div class="submit">SIGNUP NOW</div>
    <small>We respect your privacy and take protecting it seriously</small>
  </div>
  <h3 class="abs blog-title">Latest Blog</h3>
  <ul class="abs posts">
    <li><div class="thumb" role="img" aria-label="Blog photo of a bearded man" style="background:linear-gradient(135deg,#cfcfcf,#4a4a4a)"></div><div><div class="post-title">How to Use Nora's Beard Oil</div><div class="post-date">February 12, 2016</div></div></li>
    <li><div class="thumb" role="img" aria-label="Blog photo of beard oil bottles on wood" style="background:linear-gradient(135deg,#c06a2a,#2d3a6a)"></div><div><div class="post-title">How to Use Nora's Beard Oil</div><div class="post-date">February 12, 2016</div></div></li>
    <li><div class="thumb" role="img" aria-label="Blog photo of glass oil bottles" style="background:linear-gradient(135deg,#ece4d4,#b79a6a)"></div><div><div class="post-title">How to Use Nora's Beard Oil</div><div class="post-date">February 12, 2016</div></div></li>
    <li><div class="thumb" role="img" aria-label="Blog photo of a dark grooming product" style="background:linear-gradient(135deg,#6a3a5a,#1c1c2a)"></div><div><div class="post-title">How to Use Nora's Beard Oil</div><div class="post-date">February 12, 2016</div></div></li>
    <li><div class="thumb" role="img" aria-label="Blog photo of herbs and spices" style="background:linear-gradient(135deg,#c89a5a,#7a4a2a)"></div><div><div class="post-title">How to Use Nora's Beard Oil</div><div class="post-date">February 12, 2016</div></div></li>
    <li><div class="thumb" role="img" aria-label="Blog photo of amber dropper bottles" style="background:linear-gradient(135deg,#f3efe6,#d08a1a)"></div><div><div class="post-title">How to Use Nora's Beard Oil</div><div class="post-date">February 12, 2016</div></div></li>
    <li><div class="thumb" role="img" aria-label="Blog photo of a bearded man" style="background:linear-gradient(135deg,#8a6a4a,#2a1a12)"></div><div><div class="post-title">How to Use Nora's Beard Oil</div><div class="post-date">February 12, 2016</div></div></li>
  </ul>
</aside>

<footer class="abs footer">
  <span>Copyright 2016 Top Whisker Tonic. All Rights Reserved.</span>
  <div class="social" aria-label="Social links"><span></span><span></span><span></span><span></span></div>
</footer>
</body>
</html>
```